Quillmoor Air Business Card Design

Design new, 2 sides, business cards for a residential and light commercial heating, air conditioning contractor.

Target Market(s)

Homeowners, small businesses

Industry/Entity Type

Business

Contact Information for Business Card

Dominic Westerhall
Phone - 862-415-2736
Email
Address - PO box 518
Brightwater NJ 07912
Website - www.QuillmoorAirLLC.example

Requirements
Must have
• logo, company colors, standard size with no die cut, so I can use nova stamp

```html
<!DOCTYPE html>
<html lang="en">
<head>
<meta charset="utf-8">
<title>Quillmoor Air Business Card</title>
<link rel="stylesheet" href="https://fonts.googleapis.com/css2?family=Open+Sans:wght@400;600;700&display=swap">
<style>
  :root {
    --backdrop: #3a3633;
    --card: #0f0f0f;
    --accent: #f3a01f;
    --text-light: #f2f2f2;
    --divider: #6b4a17;
  }
  * { margin: 0; padding: 0; box-sizing: border-box; }
  html, body { width: 1200px; height: 900px; overflow: hidden; }
  body {
    background: var(--backdrop);
    font-family: "Open Sans", Arial, sans-serif;
    position: relative;
  }
  .card {
    position: absolute;
    top: 300px;
    width: 525px;
    height: 300px;
    background: var(--card);
    border-radius: 3px;
  }
  .card--details { left: 50px; }
  .card--brand { left: 625px; display: flex; align-items: center; justify-content: center; }

  .brand-name {
    font-weight: 700;
    font-size: 32px;
    color: var(--accent);
    display: flex;
    align-items: center;
    gap: 12px;
    letter-spacing: 0.5px;
    white-space: nowrap;
  }
  .brand-dot {
    width: 16px; height: 16px; border-radius: 50%;
    background: var(--accent);
  }

  .card--details .brand-area {
    position: absolute; left: 0; top: 0;
    width: 262px; height: 300px;
    display: flex; align-items: center; justify-content: center;
  }
  .card--details .brand-name { font-size: 24px; gap: 10px; }
  .card--details .brand-dot { width: 12px; height: 12px; }

  .divider {
    position: absolute; left: 262px; top: 70px;
    width: 1px; height: 160px;
    background: var(--divider);
  }
  .contact {
    position: absolute; left: 290px; top: 68px;
    color: var(--text-light);
    font-size: 12.5px; line-height: 1.35;
    white-space: nowrap;
  }
  .contact-name { color: var(--accent); font-weight: 700; font-size: 15px; }
  .contact-role { margin-bottom: 12px; }
  .contact-address { margin-bottom: 12px; }
  .contact-list { list-style: none; }
  .contact-list li { display: flex; align-items: center; gap: 8px; }
  .contact-list svg { width: 10px; height: 10px; fill: var(--accent); flex: none; }
</style>
</head>
<body>
  <section class="card card--details">
    <div class="brand-area">
      <div class="brand-name"><span class="brand-dot"></span>Quillmoor Air</div>
    </div>
    <div class="divider"></div>
    <div class="contact">
      <div class="contact-name">Dominic Westerhall</div>
      <div class="contact-role">Managing Director</div>
      <div class="contact-address">PO box 518<br>Brightwater NJ 07912</div>
      <ul class="contact-list">
        <li><svg viewBox="0 0 10 10"><path d="M2 0h2l1 3-1.5 1a6 6 0 0 0 2.5 2.5L7 5l3 1v2a2 2 0 0 1-2 2A8 8 0 0 1 0 2a2 2 0 0 1 2-2z"/></svg>862-415-2736</li>
        <li><svg viewBox="0 0 10 10"><path d="M2 0h6v3H2zM0 3.5h10V9H0zM2 5v2h6V5z"/></svg>862-415-2736</li>
        <li><svg viewBox="0 0 10 10"><path d="M0 1.5h10v7H0zM.8 2.2 5 5.5l4.2-3.3"/></svg>info@quillmoorair.example</li>
        <li><svg viewBox="0 0 10 10"><circle cx="5" cy="5" r="5"/></svg>www.QuillmoorAirLLC.example</li>
      </ul>
    </div>
  </section>

  <section class="card card--brand">
    <div class="brand-name"><span class="brand-dot"></span>Quillmoor Air</div>
  </section>
</body>
</html>
```